Modern looking signage for dental office.

Exterior signage for passing cars
Updates
Need extra days to review
Target Market(s)
Cars passing by
Font styles to use
Sans Serif
Colors
3276b5
Requirements
Must have
- Logo
- OPEN ON SUTURDAY AND SUNDAY
- NIGHT CLINIC AVAILABLE
- PLEASE USE THE FONT TYPE IN FILE 4 UPLOADED BELOW.
- (847) 302-7469
- Modern looking

```html
<!DOCTYPE html>
<html lang="en">
<head>
<meta charset="utf-8">
<title>Elm Dental – Weekend &amp; Night Clinic Sign</title>
<link rel="stylesheet" href="https://fonts.googleapis.com/css2?family=Montserrat:wght@300;500;700;800&display=swap">
<style>
  :root {
    --page-bg: #8d8d8d;
    --sign-black: #000000;
    --band-grey: #b9b9b9;
    --ink-black: #0d0d0d;
    --ink-grey: #5b5657;
    --rule-grey: #a8a8a8;
    --white: #ffffff;
    --icon-grey: #6f6f6f;
  }
  * { margin: 0; padding: 0; box-sizing: border-box; }
  html, body {
    width: 1200px; height: 1000px; overflow: hidden;
    background: var(--page-bg);
    font-family: "Montserrat", sans-serif;
  }
  .sign {
    position: absolute; left: 192px; top: 92px;
    width: 816px; height: 816px;
    background: var(--sign-black);
    overflow: hidden;
  }
  .sign-shapes { position: absolute; inset: 0; }
  .brand {
    position: absolute; left: 0; top: 30px; width: 816px; height: 170px;
  }
  .brand-circle {
    position: absolute; left: 111px; top: 4px;
    width: 124px; height: 124px; border-radius: 50%;
    border: 2px solid var(--white);
  }
  .brand-name {
    position: absolute; left: 258px; top: 25px;
    max-width: 540px;
    font-weight: 300; font-size: 66px; letter-spacing: 1px;
    color: var(--white); white-space: nowrap; line-height: 1;
  }
  .brand-tagline {
    position: absolute; left: 294px; top: 108px;
    font-weight: 500; font-size: 21px; letter-spacing: 0.5px;
    color: var(--white); white-space: nowrap;
  }
  .message {
    position: absolute; left: 0; width: 816px;
    text-align: center; white-space: nowrap; line-height: 1;
  }
  .open-on { top: 262px; font-size: 96px; font-weight: 800; color: var(--ink-black); }
  .weekend-days { top: 357px; font-size: 55px; font-weight: 800; color: var(--ink-grey); }
  .divider {
    position: absolute; left: 210px; top: 445px; width: 396px; height: 3px;
    background: var(--rule-grey);
  }
  .night-clinic { top: 476px; font-size: 54px; font-weight: 500; color: var(--ink-black); }
  .night-hours { top: 531px; font-size: 53px; font-weight: 800; color: var(--ink-grey); }
  .contact {
    position: absolute; left: 104px; top: 706px;
    display: flex; align-items: center; gap: 20px;
  }
  .contact-icon { width: 68px; height: 68px; }
  .contact-number {
    font-size: 77px; font-weight: 800; color: var(--white);
    letter-spacing: 1px; line-height: 1; white-space: nowrap;
  }
</style>
</head>
<body>
  <main class="sign">
    <svg class="sign-shapes" viewBox="0 0 816 816" width="816" height="816" aria-hidden="true">
      <defs>
        <linearGradient id="panelShade" x1="0" y1="0" x2="0" y2="1">
          <stop offset="0" stop-color="#ffffff"/>
          <stop offset="0.55" stop-color="#e6e6e6"/>
          <stop offset="1" stop-color="#cfcfcf"/>
        </linearGradient>
      </defs>
      <rect class="panel" x="0" y="170" width="816" height="520" fill="url(#panelShade)"/>
      <path class="band-top-grey" d="M0 250 Q408 160 816 250 V226 Q408 142 0 226 Z" fill="var(--band-grey)"/>
      <path class="band-top" d="M0 0 H816 V222 Q408 138 0 222 Z" fill="var(--sign-black)"/>
      <path class="band-bottom-grey" d="M0 604 Q408 724 816 604 V640 Q408 758 0 640 Z" fill="var(--band-grey)"/>
      <path class="band-bottom" d="M0 630 Q408 752 816 630 V816 H0 Z" fill="var(--sign-black)"/>
    </svg>

    <header class="brand">
      <div class="brand-circle"></div>
      <div class="brand-name">ELM DENTAL</div>
      <div class="brand-tagline">MODERN GENERAL DENTISTRY</div>
    </header>

    <h1 class="message open-on">OPEN ON</h1>
    <p class="message weekend-days">SATURDAY AND SUNDAY</p>
    <div class="divider"></div>
    <p class="message night-clinic">NIGHT CLINIC FROM</p>
    <p class="message night-hours">5PM TO 10PM AVAILABLE</p>

    <div class="contact">
      <svg class="contact-icon" viewBox="0 0 68 68" aria-hidden="true">
        <circle cx="34" cy="34" r="31" fill="var(--icon-grey)" stroke="var(--white)" stroke-width="3"/>
        <path d="M24 20 l6 -2 l4 9 l-4 3 q3 7 10 10 l3 -4 l9 4 l-2 6 q-3 3 -8 2 q-13 -4 -20 -18 q-2 -6 2 -10 Z" fill="var(--white)"/>
        <path d="M38 22 q7 1 9 8" stroke="var(--white)" stroke-width="2.5" fill="none" stroke-linecap="round"/>
        <path d="M39 16 q12 2 14 14" stroke="var(--white)" stroke-width="2.5" fill="none" stroke-linecap="round"/>
      </svg>
      <span class="contact-number">847 302 7469</span>
    </div>
  </main>
</body>
</html>
```